Stationery for a private security company, "Brenmoor Security Services Ltd."

Needed is a stationery design for a private security company. The designs must show professionalism and that our company mean nothing but business. Watermark of the company logo on the letterhead page is also a must. The final design must represent innovation and professionalism. It would be great if designers could integrate the colours black and silver onto the cards and letterheads..

Thank you

```html
<!DOCTYPE html>
<html lang="en">
<head>
<meta charset="utf-8">
<title>Brenmoor Security Services Ltd. — Stationery</title>
<link rel="stylesheet" href="https://fonts.googleapis.com/css2?family=Arimo:wght@400;700&display=swap">
<style>
  :root{
    --backdrop:#a9aaae;
    --folder:#2f3035;
    --folder-inner:#2a2b30;
    --pocket:#26272b;
    --paper:#ffffff;
    --ink:#1f1f22;
    --ink-soft:#555559;
    --silver:#c9cacd;
    --silver-light:#e6e7ea;
    --watermark-light:rgba(0,0,0,0.06);
    --watermark-dark:rgba(255,255,255,0.05);
  }
  *{box-sizing:border-box;margin:0;padding:0}
  html,body{width:1200px;height:983px;overflow:hidden}
  body{background:var(--backdrop);font-family:"Arimo",Arial,sans-serif;color:var(--ink);position:relative}
  .piece{position:absolute;overflow:hidden}

  /* brand lockup */
  .lockup{position:absolute;left:0;right:0;text-align:center;font-weight:700;text-transform:uppercase;line-height:1}
  .lockup .mark{display:block;margin:0 auto 6px;border-radius:50%;background:currentColor}
  .lockup .name{display:block;letter-spacing:.06em}
  .lockup .sub{display:block;letter-spacing:.02em;margin-top:3px}
  .tagline{position:absolute;left:0;right:0;text-align:center;font-weight:400;white-space:nowrap}
  .watermark{position:absolute;left:0;right:0;text-align:center;font-weight:700;text-transform:uppercase;line-height:1.1;letter-spacing:.04em;white-space:nowrap}

  /* open folder */
  .folder-open{left:217px;top:250px;width:711px;height:492px;background:var(--folder-inner)}
  .folder-open .spine{position:absolute;left:355px;top:0;bottom:0;width:1px;background:#1d1e21}
  .folder-open .pocket-left{position:absolute;left:0;top:305px;width:355px;height:187px;background:var(--pocket)}
  .folder-open .pocket-right{position:absolute;left:356px;top:305px;width:355px;height:187px;background:var(--pocket);border-top:1px solid #3a3b40}
  .folder-open .card-slot{position:absolute;left:240px;top:345px;width:75px;height:60px;border:1px solid #1c1d20;border-bottom:none}
  .folder-open .sheet{position:absolute;left:369px;top:8px;width:330px;height:334px;background:var(--paper)}
  .folder-open .closure{position:absolute;left:560px;top:325px;width:28px;height:28px;border-radius:50%;background:#1e1f22}
  .folder-open .closure-slot{position:absolute;left:560px;top:455px;width:28px;height:14px;border-radius:14px 14px 0 0;background:#1e1f22}
  .folder-open .address{position:absolute;left:600px;top:398px;width:100px;font-size:5.5px;line-height:1.35;color:var(--silver-light)}

  /* folder cover */
  .folder-cover{left:178px;top:198px;width:328px;height:478px;background:var(--folder)}
  .folder-cover .lockup{top:66px;color:var(--silver-light)}
  .folder-cover .mark{width:14px;height:14px}
  .folder-cover .name{font-size:22px}
  .folder-cover .sub{font-size:9.5px}
  .folder-cover .tagline{top:152px;font-size:9px;color:var(--silver)}
  .folder-cover .watermark{top:305px;font-size:38px;color:var(--watermark-dark)}
  .folder-cover .watermark small{display:block;font-size:15px}

  /* letterhead */
  .letterhead{left:680px;top:50px;width:328px;height:475px;background:var(--paper)}
  .letterhead .lockup{top:20px;color:var(--ink)}
  .letterhead .mark{width:12px;height:12px}
  .letterhead .name{font-size:14px}
  .letterhead .sub{font-size:6.5px}
  .letterhead .tagline{top:73px;font-size:7.5px;color:var(--ink)}
  .letterhead .watermark{top:255px;font-size:36px;color:var(--watermark-light)}
  .letterhead .watermark small{display:block;font-size:15px}
  .letterhead .rule{position:absolute;left:16px;right:16px;top:441px;height:2px;background:var(--silver)}
  .letterhead .footer{position:absolute;left:0;right:0;top:450px;text-align:center;font-size:4.6px;line-height:1.5;color:var(--ink-soft)}
  .letterhead .footer b{color:var(--ink)}

  /* business card front */
  .card-light{left:549px;top:50px;width:82px;height:145px;background:var(--paper)}
  .card-light .lockup{top:10px;color:var(--ink)}
  .card-light .mark{width:7px;height:7px;margin-bottom:3px}
  .card-light .name{font-size:7.5px}
  .card-light .sub{font-size:3.6px}
  .card-light .tagline{top:37px;font-size:4px}
  .card-light .person{position:absolute;left:0;right:0;top:57px;text-align:center;font-size:4.6px;font-weight:700}
  .card-light .role{position:absolute;left:0;right:0;top:63px;text-align:center;font-size:3.4px;color:var(--ink-soft)}
  .card-light .rule{position:absolute;left:14px;right:14px;top:95px;height:1px;background:var(--silver)}
  .card-light .details{position:absolute;left:0;right:0;top:102px;text-align:center;font-size:3.2px;line-height:1.45;color:var(--ink-soft)}
  .card-light .details b{color:var(--ink)}

  /* business card back */
  .card-dark{left:966px;top:574px;width:80px;height:142px;background:var(--folder)}
  .card-dark .lockup{top:12px;color:var(--silver-light)}
  .card-dark .mark{width:7px;height:7px;margin-bottom:3px}
  .card-dark .name{font-size:7.5px}
  .card-dark .sub{font-size:3.6px}
  .card-dark .tagline{top:38px;font-size:4px;color:var(--silver)}
  .card-dark .watermark{top:92px;font-size:10px;letter-spacing:.02em;color:var(--watermark-dark)}

  /* envelopes */
  .envelope-front{left:221px;top:765px;width:334px;height:177px;background:var(--paper)}
  .envelope-front .lockup{top:16px;left:0;right:auto;width:124px;color:var(--ink)}
  .envelope-front .mark{width:11px;height:11px}
  .envelope-front .name{font-size:13px}
  .envelope-front .sub{font-size:6px}
  .envelope-front .tagline{top:76px;left:0;right:auto;width:124px;font-size:7px}
  .envelope-front .watermark{top:10px;left:150px;right:auto;font-size:28px;color:var(--watermark-light);text-align:left}
  .envelope-front .rule{position:absolute;left:26px;top:135px;width:86px;height:2px;background:var(--silver)}
  .envelope-front .return{position:absolute;left:26px;top:144px;font-size:4.4px;line-height:1.6;color:var(--ink-soft)}
  .envelope-back{left:587px;top:766px;width:333px;height:177px;background:var(--paper)}
  .envelope-back svg{position:absolute;left:0;top:0}
  .envelope-back .seal{position:absolute;left:159px;top:18px;width:14px;height:14px;border-radius:50%;background:var(--ink)}
</style>
</head>
<body>

<section class="piece folder-open" aria-label="Presentation folder, open">
  <div class="pocket-left"></div>
  <div class="card-slot"></div>
  <div class="spine"></div>
  <div class="sheet"></div>
  <div class="pocket-right"></div>
  <div class="closure"></div>
  <div class="closure-slot"></div>
  <p class="address">Atelier Varenne<br>Rue des Lilas<br>Lyon Cedex 210<br>France 69002</p>
</section>

<section class="piece folder-cover" aria-label="Presentation folder cover">
  <div class="lockup"><span class="mark"></span><span class="name">Brenmoor</span><span class="sub">Security Services Ltd.</span></div>
  <p class="tagline">Vigilance You Can Rely On</p>
  <div class="watermark">Brenmoor<small>Security Services Ltd.</small></div>
</section>

<section class="piece card-light" aria-label="Business card">
  <div class="lockup"><span class="mark"></span><span class="name">Brenmoor</span><span class="sub">Security Services Ltd.</span></div>
  <p class="tagline">Vigilance You Can Rely On</p>
  <p class="person">CALUM ORTEN</p>
  <p class="role">Managing Director</p>
  <div class="rule"></div>
  <p class="details"><b>Mobile:</b> +44 20 7946 0111<br><b>Email:</b> calum@brenmoor.com<br><br>Unit 12, Harrow Court,<br>Leeds LS1 4AB<br><b>Phone:</b> +44 20 7946 0000<br><b>Web:</b> www.brenmoor.com</p>
</section>

<section class="piece letterhead" aria-label="Letterhead">
  <div class="lockup"><span class="mark"></span><span class="name">Brenmoor</span><span class="sub">Security Services Ltd.</span></div>
  <p class="tagline">Vigilance You Can Rely On</p>
  <div class="watermark">Brenmoor<small>Security Services Ltd.</small></div>
  <div class="rule"></div>
  <p class="footer">Unit 12, Harrow Court, Kirkgate Business Park, Leeds LS1 4AB<br><b>Phone:</b> +44 20 7946 0000 &nbsp;<b>Email:</b> info@brenmoor.com &nbsp;<b>Web:</b> www.brenmoor.com</p>
</section>

<section class="piece card-dark" aria-label="Business card reverse">
  <div class="lockup"><span class="mark"></span><span class="name">Brenmoor</span><span class="sub">Security Services Ltd.</span></div>
  <p class="tagline">Vigilance You Can Rely On</p>
  <div class="watermark">Brenmoor</div>
</section>

<section class="piece envelope-front" aria-label="Envelope front">
  <div class="watermark">Brenmoor</div>
  <div class="lockup"><span class="mark"></span><span class="name">Brenmoor</span><span class="sub">Security Services Ltd.</span></div>
  <p class="tagline">Vigilance You Can Rely On</p>
  <div class="rule"></div>
  <p class="return">Unit 12, Harrow Court, Kirkgate Park<br>Leeds LS1 4AB</p>
</section>

<section class="piece envelope-back" aria-label="Envelope back">
  <svg width="333" height="177" viewBox="0 0 333 177" aria-hidden="true">
    <polyline points="0,1 166,70 333,1" fill="none" stroke="#d8d9dc" stroke-width="1.2"/>
  </svg>
  <div class="seal"></div>
</section>

</body>
</html>
```